Update our OBGYN business card look and info

We are an OBGYN office. Our logo is nice but would like to "woman" part of the logo to be a darker color, to contrast with the flower that surrounds it. Maybe make our practice name Bloom Harbor Health more feminine. Our practice caters to women only. All providers and staff are female.

Target Market(s)

Females 16-65.

Industry/Entity Type

Business

Contact Information for Business Card

See attached upload. The ONLY CHANGE to the information is DELETE the name Paula Renwick, Midwife and REPLACE with Dora Fintelli, Midwife

Logo Text

Bloom Harbor Health Obstetrics & Gynecology

Font styles to use
Serif
Script

Colors
85cae6
0692cd
33a6d7
85abd2
f59195
eea4c8
cadf82
fac994
d3a5cc

```html
<!DOCTYPE html>
<html lang="en">
<head>
<meta charset="utf-8">
<title>Bloom Harbor Health — Business Card</title>
<link href="https://fonts.googleapis.com/css2?family=Cinzel:wght@400&family=Lora:wght@400&family=Open+Sans:wght@400&display=swap" rel="stylesheet">
<style>
  :root {
    --backdrop: #0b0b0b;
    --card-white: #f4f5f6;
    --blush: #f59195;
    --blush-deep: #f28a90;
    --ink: #5a5a5a;
    --ink-soft: #6b6b6b;
    --white: #ffffff;
  }
  * { box-sizing: border-box; margin: 0; padding: 0; }
  html, body {
    width: 1200px; height: 1000px; overflow: hidden;
    background: var(--backdrop);
  }
  .stage {
    position: relative; width: 1200px; height: 1000px;
    display: flex; align-items: center; justify-content: center; gap: 60px;
  }
  .card {
    position: relative; width: 500px; height: 290px;
    border-radius: 22px; overflow: hidden;
    box-shadow: 0 14px 30px rgba(0,0,0,.55);
  }

  /* Front */
  .card-front { background: var(--card-white); }
  .brand {
    position: absolute; left: 34px; top: 30px;
    display: flex; align-items: center; gap: 12px;
  }
  .brand-dot {
    width: 34px; height: 34px; border-radius: 50%;
    background: var(--blush);
  }
  .brand-name {
    font-family: "Cinzel", serif; font-weight: 400;
    font-size: 19px; letter-spacing: .5px; color: var(--blush);
    line-height: 1.1;
  }
  .brand-sub {
    font-family: "Open Sans", sans-serif; font-size: 14px;
    color: var(--ink); margin-top: 3px;
  }
  .accent-bar {
    position: absolute; left: 0; top: 108px;
    width: 16px; height: 30px; background: var(--blush);
  }
  .address {
    position: absolute; left: 34px; top: 108px;
    font-family: "Open Sans", sans-serif; font-size: 12.5px;
    color: var(--ink); line-height: 1.3;
  }
  .contacts {
    position: absolute; left: 34px; top: 162px;
    list-style: none;
    font-family: "Open Sans", sans-serif; font-size: 12px; color: var(--ink);
  }
  .contacts li { display: flex; align-items: center; gap: 9px; line-height: 1.45; }
  .contacts svg { width: 11px; height: 11px; fill: var(--blush); flex: none; }
  .providers {
    position: absolute; right: 36px; bottom: 28px;
    list-style: none; text-align: right;
    font-family: "Lora", serif; font-size: 14.5px; color: var(--ink-soft);
    line-height: 1.32;
  }

  /* Back */
  .card-back {
    background: linear-gradient(100deg, var(--blush-deep), #f59ba0 45%, var(--blush));
    display: flex; align-items: center; justify-content: center; gap: 14px;
  }
  .back-dot {
    width: 40px; height: 40px; border-radius: 50%; background: var(--white);
  }
  .back-name {
    font-family: "Cinzel", serif; font-weight: 400;
    font-size: 26px; letter-spacing: 1px; color: var(--white);
  }
</style>
</head>
<body>
<main class="stage">
  <section class="card card-front" aria-label="Business card front">
    <div class="brand">
      <span class="brand-dot"></span>
      <div>
        <div class="brand-name">Bloom Harbor Health</div>
        <div class="brand-sub">Obstetrics &amp; Gynecology</div>
      </div>
    </div>

    <span class="accent-bar"></span>
    <address class="address" style="font-style:normal">
      2148 Larkspur Avenue<br>
      Suite 3B Halden, GA 30917
    </address>

    <ul class="contacts">
      <li>
        <svg viewBox="0 0 24 24" aria-hidden="true"><path d="M6.6 10.8a15.1 15.1 0 0 0 6.6 6.6l2.2-2.2c.3-.3.7-.4 1-.2 1.1.4 2.3.6 3.6.6.6 0 1 .4 1 1V20c0 .6-.4 1-1 1A17 17 0 0 1 3 4c0-.6.4-1 1-1h3.5c.6 0 1 .4 1 1 0 1.3.2 2.5.6 3.6.1.3 0 .7-.2 1z"/></svg>
        555 210 4837
      </li>
      <li>
        <svg viewBox="0 0 24 24" aria-hidden="true"><path d="M6 2h12v6H6zM3 9h18a1 1 0 0 1 1 1v8h-4v4H6v-4H2v-8a1 1 0 0 1 1-1zm5 8v3h8v-3z"/></svg>
        555 210 4912
      </li>
      <li>
        <svg viewBox="0 0 24 24" aria-hidden="true"><path d="M12 2a10 10 0 1 0 0 20 10 10 0 0 0 0-20zm6.9 9h-3a15 15 0 0 0-1.3-5.6A8 8 0 0 1 18.9 11zM12 4c.9 1.3 1.7 3.6 1.9 7h-3.8c.2-3.4 1-5.7 1.9-7zM9.4 5.4A15 15 0 0 0 8.1 11h-3a8 8 0 0 1 4.3-5.6zM5.1 13h3a15 15 0 0 0 1.3 5.6A8 8 0 0 1 5.1 13zm6.9 7c-.9-1.3-1.7-3.6-1.9-7h3.8c-.2 3.4-1 5.7-1.9 7zm2.6-1.4a15 15 0 0 0 1.3-5.6h3a8 8 0 0 1-4.3 5.6z"/></svg>
        www.bloomharborhealth.com
      </li>
    </ul>

    <ul class="providers">
      <li>Marian Ostrel, MD</li>
      <li>Lena Varholt, MD</li>
      <li>Irene Solbeck, MD</li>
      <li>Dora Fintelli, Midwife</li>
      <li>Nadia Corvell, Midwife</li>
    </ul>
  </section>

  <section class="card card-back" aria-label="Business card back">
    <span class="back-dot"></span>
    <span class="back-name">Bloom Harbor Health</span>
  </section>
</main>
</body>
</html>
```